Online business manager needs a website

I need a website designed and then coded. I am an online business manager serving a number of different industries providing administrative support to existing small businesses and helping solo practitioners get their new business up and running.

I didn't have a logo formally designed but have been using the attached avatar and wouldn't mind something that incorporated that.

The business doesn't have an official name, so I've just been using my name Lena Morvath, Online Business Manager or Lena Morvath, OBM. I've attached two documents that I have made previously for an example of content.

I would prefer the final site be in Wordpress.

Requirements
Must have
• A way to contact me, testimonials, list of services

```html
<!DOCTYPE html>
<html lang="en">
<head>
<meta charset="utf-8">
<title>Lena Morvath | OBM</title>
<link href="https://fonts.googleapis.com/css2?family=Montserrat:wght@600;700;800&family=Mulish:wght@400;600;700&display=swap" rel="stylesheet">
<style>
:root{
  --orange:#f7a01b;
  --navy:#2c4260;
  --ink:#1f1f1f;
  --muted:#444;
  --soft:#f5f3f3;
  --card-line:#e6e4e4;
  --peach:#fdf0e1;
  --purple:#4b2a8f;
}
*{box-sizing:border-box;margin:0;padding:0}
html,body{width:1200px;height:4161px;overflow:hidden}
body{font-family:"Mulish",sans-serif;color:var(--ink);background:#fff;position:relative}
.abs{position:absolute}
h2.section-title{font-family:"Montserrat",sans-serif;font-weight:700;font-size:24px;letter-spacing:.3px;text-align:center;position:absolute;left:0;width:1200px}
.title-rule{position:absolute;left:584px;width:32px;height:2px;background:var(--navy)}
.btn{position:absolute;background:var(--orange);color:#fff;font-family:"Montserrat",sans-serif;font-weight:700;font-size:14px;letter-spacing:.5px;display:flex;align-items:center;justify-content:center}

/* hero */
.hero{position:absolute;left:0;top:0;width:1200px;height:630px}
.hero-bg{position:absolute;inset:0;background:linear-gradient(160deg,#3a4048 0%,#23282f 45%,#3e3a36 100%)}
.hero-portrait{position:absolute;left:700px;top:60px;width:500px;height:570px;background:radial-gradient(ellipse at 55% 35%,#c9a088 0%,#8a6e62 35%,#2b2b33 75%);border-radius:240px 240px 0 0}
.brand{position:absolute;font-family:"Montserrat",sans-serif;font-weight:700;font-size:24px;color:#fff;display:flex;align-items:center;gap:10px}
.brand small{font-family:"Mulish",sans-serif;font-weight:400;font-size:19px;border-left:2px solid #fff;padding-left:9px;line-height:20px}
.nav{position:absolute;font-size:14px;color:#fff}
.nav.active{color:var(--orange)}
.nav.active::after{content:"";position:absolute;left:0;right:0;top:24px;height:2px;background:var(--orange)}
.hero h1{position:absolute;left:132px;top:226px;font-family:"Montserrat",sans-serif;font-weight:700;font-size:39px;color:#fff;letter-spacing:.2px}
.hero p{position:absolute;left:132px;top:288px;width:520px;font-size:17px;line-height:21.5px;color:#fff}

/* services */
.services{position:absolute;left:0;top:630px;width:1200px;height:598px;background:var(--soft)}
.services-panel{position:absolute;left:58px;top:0;width:1082px;height:598px;background:#fff;border-radius:0 0 50px 50px}
.services-top{position:absolute;left:0;top:0;width:1200px;height:490px;background:#fff}
.card{position:absolute;width:456px;height:207px;background:#fff;border:1px solid var(--card-line);box-shadow:0 2px 6px rgba(0,0,0,.06)}
.card .icon{position:absolute;left:25px;top:40px;width:110px;height:110px;border-radius:50%;background:var(--peach);display:flex;align-items:center;justify-content:center}
.card h3{position:absolute;left:167px;font-family:"Montserrat",sans-serif;font-weight:700;font-size:15.5px;line-height:19px;width:260px}
.card ul{position:absolute;left:167px;list-style:none;font-size:12.5px;line-height:27px}
.card li{padding-left:16px;position:relative}
.card li::before{content:"";position:absolute;left:0;top:11px;width:7px;height:7px;border-radius:50%;background:var(--orange)}

/* about */
.about{position:absolute;left:0;top:1228px;width:1200px;height:403px;background:var(--soft)}
.about-photo{position:absolute;left:132px;top:30px;width:348px;height:348px;border-radius:50%;background:radial-gradient(circle at 50% 45%,#d7b59a 0%,#9a7562 30%,#3b2f6b 65%,#1b1740 100%)}
.about h2{position:absolute;left:525px;top:45px;font-family:"Montserrat",sans-serif;font-weight:700;font-size:24px}
.about p{position:absolute;left:525px;top:110px;width:538px;font-size:13.8px;line-height:21.6px;text-align:justify;color:var(--muted)}

/* rates */
.rate{position:absolute;top:1751px;width:224px;height:206px;background:#fff;border:1px solid var(--card-line);text-align:center}
.rate .price{position:absolute;left:0;right:0;top:22px;font-family:"Montserrat",sans-serif;font-weight:700;font-size:29px;color:var(--orange)}
.rate .pill{position:absolute;left:50%;transform:translateX(-50%);top:76px;border:1px solid #bbb;font-size:12px;padding:3px 8px;white-space:nowrap;color:#333}
.rate .desc{position:absolute;left:20px;right:20px;top:122px;font-size:14px;line-height:22px;color:#333}
.rate .foot{position:absolute;left:0;right:0;bottom:0;height:26px;background:var(--soft);font-size:11.5px;line-height:26px;color:#333}

/* testimonials */
.testimonials{position:absolute;left:0;top:1975px;width:1200px;height:529px;background:var(--navy);color:#fff;text-align:center}
.testimonials .waves{position:absolute;left:0;top:0}
.testimonials h2{position:absolute;left:0;width:1200px;top:78px;font-family:"Montserrat",sans-serif;font-weight:700;font-size:23px}
.testimonials .rule{position:absolute;left:584px;top:117px;width:32px;height:2px;background:#fff}
.avatar{position:absolute;left:553px;top:153px;width:94px;height:94px;border-radius:50%;background:radial-gradient(circle at 50% 40%,#c8936f 0%,#8c5b43 45%,#d7c7b3 100%)}
.quote-mark{position:absolute;left:0;width:1200px;top:255px;font-family:"Montserrat",sans-serif;font-weight:800;font-size:56px;line-height:56px;color:var(--orange)}
.testimonials blockquote{position:absolute;left:270px;width:660px;top:316px;font-size:19px;line-height:29px}
.testimonials .line{position:absolute;left:446px;top:453px;width:276px;height:2px;background:var(--orange)}
.testimonials cite{position:absolute;left:0;width:1200px;top:472px;font-style:normal;font-weight:700;font-size:13.5px}

/* work */
.work-tile{position:absolute}

/* contact */
.contact-photo{position:absolute;left:0;top:3416px;width:596px;height:601px;background:linear-gradient(135deg,#5a4a40 0%,#b08f78 45%,#7d6a60 70%,#3e3a3d 100%)}
.contact-panel{position:absolute;left:596px;top:3416px;width:604px;height:601px;background:var(--soft)}
.contact h2{position:absolute;left:648px;top:3455px;font-family:"Montserrat",sans-serif;font-weight:700;font-size:23px}
.contact .rule{position:absolute;left:648px;top:3487px;width:32px;height:2px;background:var(--navy)}
.contact-item{position:absolute;left:648px;display:flex;align-items:center;gap:17px;font-size:19px;color:#222}
.contact-item .ic{width:36px;height:36px;border-radius:5px;background:var(--purple);display:flex;align-items:center;justify-content:center}
.field{position:absolute;background:#fff;border:1px solid #c9c9c9;font-size:11px;color:#444;padding:0 12px;display:flex;align-items:center}
.field.textarea{align-items:flex-start;padding-top:11px}

/* footer */
.footer{position:absolute;left:0;top:4017px;width:1200px;height:144px;background:var(--navy);color:#fff}
.footer .rule{position:absolute;left:132px;top:79px;width:941px;height:1px;background:rgba(255,255,255,.55)}
.footer .copy{position:absolute;left:0;width:1200px;top:105px;text-align:center;font-size:12px}
</style>
</head>
<body>

<!-- Hero -->
<header class="hero">
  <div class="hero-bg" role="img" aria-label="City skyline seen through tall office windows at dusk"></div>
  <div class="hero-portrait" role="img" aria-label="Portrait of Lena Morvath smiling, wearing glasses and a polka dot top"></div>
  <div class="brand" style="left:132px;top:24px">LENA MORVATH <small>OBM</small></div>
  <span class="nav active" style="left:632px;top:23px">Home</span>
  <span class="nav" style="left:705px;top:23px">About Me</span>
  <span class="nav" style="left:809px;top:23px">Services</span>
  <span class="nav" style="left:897px;top:23px">My Work</span>
  <span class="nav" style="left:993px;top:23px">Contact Me</span>
  <h1>ONLINE BUSINESS MANAGER</h1>
  <p>Focused on the live event and entertainment industry. Helping artists and owners to better manage their career and business by strategically reviewing systems, recommending operational efficiencies, and managing inboxes</p>
  <div class="btn" style="left:132px;top:399px;width:133px;height:36px">READ MORE</div>
</header>

<!-- Services -->
<section class="services">
  <div class="services-top"></div>
  <div class="services-panel"></div>
  <h2 class="section-title" style="top:35px">SERVICES</h2>
  <div class="title-rule" style="top:80px"></div>

  <div class="card" style="left:132px;top:116px">
    <div class="icon"><svg width="60" height="60" viewBox="0 0 60 60" fill="none" stroke="#f7a01b" stroke-width="2"><rect x="8" y="12" width="44" height="30" rx="2"/><path d="M24 50h12M30 42v8"/><circle cx="30" cy="24" r="5"/><path d="M21 37c2-5 16-5 18 0"/></svg></div>
    <h3 style="top:38px">Virtual Assistance</h3>
    <ul style="top:64px"><li>Calendar Management</li><li>Email Management</li><li>Light Graphic Design</li><li>Data Entry</li></ul>
  </div>
  <div class="card" style="left:612px;top:116px">
    <div class="icon"><svg width="60" height="60" viewBox="0 0 60 60" fill="none" stroke="#f7a01b" stroke-width="2"><circle cx="30" cy="16" r="7"/><rect x="8" y="28" width="20" height="22" rx="2"/><rect x="32" y="32" width="20" height="16" rx="2"/><path d="M39 36l6 4-6 4z"/><path d="M12 35h12M12 40h12M12 45h8"/></svg></div>
    <h3 style="top:20px">Social Media &amp; Content Management</h3>
    <ul style="top:64px"><li>Content Repurposing</li><li>Graphics Creation</li><li>Audiogram Creation</li><li>Search Engine Optimization</li></ul>
  </div>
  <div class="card" style="left:132px;top:345px">
    <div class="icon"><svg width="60" height="60" viewBox="0 0 60 60" fill="none" stroke="#f7a01b" stroke-width="2"><circle cx="20" cy="18" r="8"/><circle cx="38" cy="30" r="8"/><circle cx="22" cy="42" r="8"/><path d="M46 30h8M50 20v20"/></svg></div>
    <h3 style="top:36px">Finance Management</h3>
    <ul style="top:62px"><li>Create Invoices</li><li>Track Receivables</li><li>Analyze Expenses</li><li>Year Over Year Analytics</li></ul>
  </div>
  <div class="card" style="left:612px;top:345px">
    <div class="icon"><svg width="60" height="60" viewBox="0 0 60 60" fill="none" stroke="#f7a01b" stroke-width="2"><circle cx="24" cy="22" r="9"/><circle cx="24" cy="22" r="3"/><circle cx="38" cy="40" r="9"/><circle cx="38" cy="40" r="3"/><path d="M24 9v4M24 31v4M11 22h4M33 22h4M38 27v4M38 49v4M25 40h4M47 40h4"/></svg></div>
    <h3 style="top:34px">Business Management</h3>
    <ul style="top:62px"><li>Creation of Operating Procedures</li><li>Review of Website Strategy</li><li>Reporting and Analytics</li><li>Project Management</li></ul>
  </div>
</section>

<!-- About -->
<section class="about">
  <div class="about-photo" role="img" aria-label="Portrait of Lena Morvath against a starry galaxy background"></div>
  <h2>ABOUT ME</h2>
  <p>Hi! I'm so excited that you have chosen to explore my portfolio. Helping businesses achieve their goals is my passion, and I'm thrilled that with my assistance you will have more time for your own passion project. I thrive while working independently, which means you can be confident when leaving tasks for me. The type of work that lights me up is anything involving organization and/or spreadsheets. You need data analyzed that includes multiple nested if formulas? You have an overwhelming amount of email to sort through and appointments to book? I'm your gal!</p>
  <div class="btn" style="left:526px;top:313px;width:123px;height:34px;font-size:13px">READ MORE</div>
</section>

<!-- Rates -->
<section class="rates">
  <h2 class="section-title" style="top:1670px">RATES AND PACKAGES</h2>
  <div class="title-rule" style="top:1718px"></div>
  <div class="rate" style="left:132px"><div class="price">$40</div><div class="pill">Hourly Rate</div><div class="desc">For clients needing only occasional help</div></div>
  <div class="rate" style="left:370px"><div class="price">$700</div><div class="pill">20 hours/month</div><div class="desc">Includes one 15 minute meeting per week</div><div class="foot">Responses within 72 hours</div></div>
  <div class="rate" style="left:606px"><div class="price">$1,300</div><div class="pill">40 hours/month</div><div class="desc">Includes one 30 minute meeting per week</div><div class="foot">Responses within 48 hours</div></div>
  <div class="rate" style="left:843px"><div class="price">$2,400</div><div class="pill">80 hours/month</div><div class="desc">Includes one 60 minute meeting per week</div><div class="foot">Responses within 24 hours</div></div>
</section>

<!-- Testimonials -->
<section class="testimonials">
  <svg class="waves" width="1200" height="46" viewBox="0 0 1200 46"><path d="M0 0H1200V20C1170 10 1150 38 1120 30 1080 18 1040 42 1000 34 960 26 940 12 900 24 860 36 820 14 780 22 740 30 700 8 660 20 620 32 580 12 540 26 500 38 460 14 420 22 380 30 340 40 300 24 260 12 220 36 180 30 150 26 120 12 90 24 60 34 30 18 0 26Z" fill="#fff"/></svg>
  <h2>TESTIMONIALS</h2>
  <div class="rule"></div>
  <div class="avatar" role="img" aria-label="Portrait of the client giving the testimonial"></div>
  <div class="quote-mark">&ldquo;</div>
  <blockquote>When it became apparent that a project would take more time than I had, Lena stepped up to take on the required research. She was thorough and timely; able to meet a last-minute 12-hour deadline. I would highly recommend Lena to assist with your next project.</blockquote>
  <div class="line"></div>
  <cite>Dana R. Owner, Summit Ridge Roofing</cite>
</section>

<!-- My Work -->
<section class="work">
  <h2 class="section-title" style="top:2541px">MY WORK</h2>
  <div class="title-rule" style="top:2589px"></div>
  <div class="work-tile" style="left:132px;top:2627px;width:265px;height:262px;background:linear-gradient(135deg,#fbeee6,#f3ddd2)" role="img" aria-label="Podcast episode graphic about owning business workflows and automations"></div>
  <div class="work-tile" style="left:409px;top:2627px;width:313px;height:262px;background:#f25c5a" role="img" aria-label="Quote graphic with coral background"></div>
  <div class="work-tile" style="left:733px;top:2627px;width:335px;height:290px;background:#fd8c45" role="img" aria-label="Blog title graphic on an orange background"></div>
  <div class="work-tile" style="left:132px;top:2900px;width:406px;height:227px;background:linear-gradient(120deg,#8fa64a,#c7c6a6)" role="img" aria-label="Photo of a playful dog lying on grass"></div>
  <div class="work-tile" style="left:538px;top:2900px;width:184px;height:227px;background:#2f9aa6" role="img" aria-label="Animal rescue adoption promo panel"></div>
  <div class="work-tile" style="left:733px;top:2917px;width:335px;height:210px;background:linear-gradient(90deg,#6b8f96,#a7b6b7 50%,#6f9a9e)" role="img" aria-label="Side by side video call comparison photos"></div>
  <div class="work-tile" style="left:132px;top:3145px;width:220px;height:219px;background:#f3efe9" role="img" aria-label="Podcast announcement graphic with guest photos"></div>
  <div class="work-tile" style="left:375px;top:3222px;width:69px;height:68px;background:var(--purple);border-radius:8px" role="img" aria-label="App badge"></div>
  <div class="work-tile" style="left:468px;top:3140px;width:600px;height:224px;background:linear-gradient(135deg,#ebcbcd,#e6c2c5)" role="img" aria-label="Podcast cover with headphones and keyboard on a pink desk"></div>
</section>

<!-- Contact -->
<section class="contact">
  <div class="contact-photo" role="img" aria-label="Photo of Lena Morvath smiling on a city street"></div>
  <div class="contact-panel"></div>
  <h2>CONTACT ME</h2>
  <div class="rule"></div>
  <div class="contact-item" style="top:3503px"><span class="ic"><svg width="20" height="20" viewBox="0 0 24 24" fill="#fff"><path d="M6.6 10.8c1.4 2.8 3.8 5.1 6.6 6.6l2.2-2.2c.3-.3.7-.4 1-.2 1.1.4 2.3.6 3.6.6.6 0 1 .4 1 1V20c0 .6-.4 1-1 1C10.6 21 3 13.4 3 4c0-.6.4-1 1-1h3.5c.6 0 1 .4 1 1 0 1.3.2 2.5.6 3.6.1.3 0 .7-.2 1z"/></svg></span>555.204.8816</div>
  <div class="contact-item" style="top:3551px"><span class="ic"><svg width="20" height="16" viewBox="0 0 24 18" fill="none" stroke="#fff" stroke-width="2"><rect x="1" y="1" width="22" height="16" rx="2"/><path d="M1 2l11 8 11-8"/></svg></span>lena.morvath@example.com</div>
  <div class="contact-item" style="top:3600px"><span class="ic"></span>Lena Morvath</div>
  <div class="contact-item" style="top:3647px"><span class="ic"></span>/LenaMorvathOBM</div>
  <div class="field" style="left:648px;top:3702px;width:205px;height:39px">First Name</div>
  <div class="field" style="left:864px;top:3702px;width:204px;height:39px">Last Name</div>
  <div class="field" style="left:648px;top:3752px;width:420px;height:39px">Email id</div>
  <div class="field" style="left:648px;top:3802px;width:420px;height:39px">Phone</div>
  <div class="field textarea" style="left:648px;top:3850px;width:420px;height:86px">Message</div>
  <div class="btn" style="left:648px;top:3947px;width:98px;height:37px">SUBMIT</div>
</section>

<!-- Footer -->
<footer class="footer">
  <div class="brand" style="left:132px;top:31px">LENA MORVATH <small>OBM</small></div>
  <span class="nav" style="left:632px;top:36px">Home</span>
  <span class="nav" style="left:704px;top:36px">About Me</span>
  <span class="nav" style="left:808px;top:36px">Services</span>
  <span class="nav" style="left:896px;top:36px">My Work</span>
  <span class="nav" style="left:992px;top:36px">Contact Me</span>
  <div class="rule"></div>
  <div class="copy">Copyright © 2023 All Rights Reserved</div>
</footer>

</body>
</html>
```